July 2022 Industrial Manufacturer Product Expo Mexico City

We manufacture large screws and fastners for large Mining equipment, Trains, large ships, airplanes, wind turbines, and so on. We also do custom work base on the customer needs. No matter the size we can make it.
We have a Expo coming up with companies all over the world. We have to stand out we are a family own business so our customer service will be above and beyond anyone can provide. We do not have a sales force to push our products and services we provide one on one service.
Plus@!! I'm looking for anything that you designers can come up with if it was your company to put on a business card, plus i want to do a 1 or 2 sided pamphlet, and then a website. We make Speciality Bolts for large mining equipment these bolts can be 3 to 4 foot long!!! Plus fasteners, Nuts, washers, any, size, strengths, special materials, we offer more of a ono on one customer service, We are a small company, family own, but can fulfill any type of orders. We can also provide special time lines for emergency orders. "We keep the machines running we here at KRV don't believe in down time" We want to hear any slogan based on our company to stand out.
Thanks i really appreciate all your work and options that we have to pick on. Plus just a thought we could possibly want to entertain a experience Marketing internet help maybe a employment possibility. Thanks

I need 2 cards one in Spanish and English Like the steel back ground maybe send me in some bright red and blue writing Same with the Black cards Please remove the word Military The logo KRV maybe integrate a picture of a Bolt 🔩 Thank you

Still looking for I need 2 cards one in Spanish and English Like the steel back ground maybe send me in some bright red and blue writing Same with the Black cards try bright writing Please remove the word Military The logo KRV maybe integrate a picture of a Bolt 🔩 Plus will need the company to make a brochure and website next Thank you

Target Market(s)

Large Mining, Ship, Train, Green Energy, VELM, and Government equipment. Throughout the World

Industry/Entity Type

We can Custom Manufacture any type of Fastners for Mining equipment, Trains, Ships, Green energy, Governments, or military projects. wind turbines,

Contact Information for Business Card

I attached the name and contact info that's on a card, plus the Company Logo. Would like industrial looking background with Bright Colors that will stand out!! If we can insert somewhere maybe on back that we "Custom Manufacture Any Size or Quantity Fastners for Large Mining Equipment, Trains, Ships, Green Energy Equipment or Government Projects

Font styles to use
Other font styles liked:
• You Pick, has to be bold, colorful standout, Professional looking Beable to read it.

Colors

Designer to choose colors to be used in the design.

Requirements
Must have
• Need in Spanish and English TO STANDOUT FROM THE REST OF THE EXPO!! See Business card details, Rounded corners
Nice to have
• Can i see some of the darker cards with Bright Red and Blue letters I like to see the different type of card material, heavy thickness, plastic, transparent, Metal types, Bright Colors, I saw like Raised letters like on the logo.

```html
<!DOCTYPE html>
<html lang="es">
<head>
<meta charset="utf-8">
<title>KRV – Tarjetas de presentación</title>
<link rel="stylesheet" href="https://fonts.googleapis.com/css2?family=Open+Sans:wght@400;600;700&display=swap">
<style>
  :root {
    --page: #c9c9c9;
    --paper: #ffffff;
    --navy: #0a1f8f;
    --sky: #1f8fdc;
    --deep: #0b2a9c;
    --mid: #0c52c0;
    --bright: #1590dc;
    --white: #ffffff;
  }
  * { box-sizing: border-box; margin: 0; padding: 0; }
  html, body { width: 1200px; height: 800px; overflow: hidden; }
  body {
    background: var(--page);
    font-family: "Open Sans", Arial, sans-serif;
    position: relative;
  }
  .card {
    position: absolute;
    top: 251px;
    width: 520px;
    height: 298px;
    border-radius: 10px;
    overflow: hidden;
    box-shadow: 0 10px 24px rgba(0,0,0,.28);
  }

  /* Front */
  .card-front { left: 45px; background: var(--paper); border-bottom: 3px solid var(--sky); }
  .front-brand {
    position: absolute; top: 34px; left: 0; width: 100%;
    display: flex; justify-content: center; align-items: center; gap: 14px;
  }
  .front-brand .mark { width: 20px; height: 20px; border-radius: 50%; background: var(--sky); }
  .front-brand .name {
    font-weight: 700; font-size: 64px; color: var(--sky); letter-spacing: 4px; line-height: 1;
  }
  .holder {
    position: absolute; left: 36px; top: 150px;
    font-weight: 700; font-size: 20px; line-height: 1.2; color: var(--sky);
  }
  .phones {
    position: absolute; right: 36px; top: 128px;
    color: var(--navy); font-size: 14px; line-height: 1.4;
  }
  .phones li { list-style: none; display: flex; align-items: center; justify-content: flex-end; gap: 6px; }
  .phones svg { width: 13px; height: 13px; flex: none; }
  .divider {
    position: absolute; left: 36px; right: 36px; top: 186px;
    height: 1px; background: var(--navy);
  }
  .contact {
    position: absolute; left: 48px; top: 200px;
    color: var(--navy); font-size: 16px; line-height: 1.4;
  }

  /* Back */
  .card-back {
    left: 635px;
    background: linear-gradient(200deg, var(--deep) 0%, var(--mid) 45%, var(--bright) 100%);
    border-bottom: 3px solid var(--navy);
  }
  .back-pattern {
    position: absolute; inset: 0;
    background: linear-gradient(200deg, rgba(255,255,255,.05), rgba(0,0,0,.05));
  }
  .back-brand {
    position: absolute; top: 150px; left: 0; width: 100%;
    text-align: center; color: var(--white);
    font-weight: 700; font-size: 28px; letter-spacing: 3px; line-height: 1;
  }
  .tagline {
    position: absolute; left: 22px; right: 22px; top: 196px;
    padding: 10px 12px;
    background: rgba(255,255,255,.08);
    color: var(--white); font-size: 15px; line-height: 1.4; text-align: center;
  }
</style>
</head>
<body>
  <article class="card card-front">
    <div class="front-brand">
      <span class="mark"></span>
      <span class="name">KRV</span>
    </div>
    <h1 class="holder">Lic. Daniela Ortega Ruiz</h1>
    <ul class="phones">
      <li>5550123401
        <svg viewBox="0 0 24 24"><path fill="#0a1f8f" d="M6.6 10.8a15 15 0 0 0 6.6 6.6l2.2-2.2a1 1 0 0 1 1-.25 11 11 0 0 0 3.6.6 1 1 0 0 1 1 1V20a1 1 0 0 1-1 1A17 17 0 0 1 3 4a1 1 0 0 1 1-1h3.5a1 1 0 0 1 1 1 11 11 0 0 0 .6 3.6 1 1 0 0 1-.25 1z"/></svg>
      </li>
      <li>5550198700
        <svg viewBox="0 0 24 24"><rect x="6" y="2" width="12" height="20" rx="2" fill="none" stroke="#0a1f8f" stroke-width="2"/><circle cx="12" cy="18" r="1.2" fill="#0a1f8f"/></svg>
      </li>
    </ul>
    <div class="divider"></div>
    <p class="contact">Cotizaciones en<br>ventas.krv@correo-ejemplo.mx</p>
  </article>

  <article class="card card-back">
    <div class="back-pattern" role="img" aria-label="Faint embossed repeating pattern of the company name across the blue background"></div>
    <div class="back-brand">KRV</div>
    <p class="tagline">Custom Manufacture Any Size or Quantity Fastners for Large Mining Equipment, Trains, Ships, Green Energy Equipment or Government Projects</p>
  </article>
</body>
</html>
```